Bright Nook Home Page (A Home Wellness e-commerce site & blog)

We need a dynamic home page created for a home wellness brand. Must be visually appealing and extremely mobile-friendly. Logos and a Navmap have been provided but that is just a guideline, PLEASE USE YOUR CREATIVITY.

Target Market(s)

1st target demo: females 24-48, 2nd target demo: all 24-48

Number of Pages Required

1 page

```html
<!DOCTYPE html>
<html lang="en">
<head>
<meta charset="utf-8">
<title>Bright Nook — Home Wellness</title>
<link href="https://fonts.googleapis.com/css2?family=Lexend:wght@500;600&family=Lato:wght@400;700&display=swap" rel="stylesheet">
<style>
:root{
  --purple:#4a1c89;
  --teal:#2bb3bd;
  --teal-deep:#1f9aa4;
  --ink:#1d1b1f;
  --night:#151215;
  --night-deep:#0e0c0e;
  --white:#ffffff;
  --sunset-a:#f6c65a;
  --sunset-b:#ef7a3a;
  --sunset-c:#b8323f;
  --lilac:#7c5bb5;
}
*{box-sizing:border-box;margin:0;padding:0}
html,body{width:1200px;height:3767px;overflow:hidden}
body{position:relative;background:var(--white);font-family:"Lato",sans-serif;color:var(--ink)}
.abs{position:absolute}
.heading{font-family:"Lexend",sans-serif;font-weight:600}
/* top bar */
.topbar{left:0;top:0;width:1200px;height:51px}
.topbar-note{left:74px;top:16px;font-size:15px;font-weight:700}
.social{display:flex;gap:20px}
.social span{width:20px;height:20px;border-radius:50%;background:var(--ink);display:block}
.topbar .social{position:absolute;right:74px;top:15px}
/* nav */
.nav{left:0;top:51px;width:1200px;height:117px;background:var(--purple)}
.brand{font-family:"Lexend",sans-serif;font-weight:600;color:var(--white);font-size:40px;letter-spacing:-.5px;display:flex;align-items:center;gap:12px}
.brand i{width:14px;height:14px;background:var(--teal);border-radius:50%;display:block}
.nav .brand{position:absolute;left:75px;top:32px}
.menu{position:absolute;left:489px;top:50px;display:flex;gap:50px;font-size:16px;font-weight:700;color:var(--white)}
.cart{position:absolute;left:1071px;top:44px;width:36px;height:36px;border-radius:50%;background:var(--teal)}
.cart-count{position:absolute;left:1100px;top:38px;width:22px;height:22px;border-radius:50%;background:var(--ink);color:var(--white);font-size:13px;text-align:center;line-height:22px;font-weight:700}
/* hero */
.hero{left:0;top:168px;width:1200px;height:778px}
.hero-card{left:615px;top:330px;width:512px;height:377px;background:rgba(255,236,170,.55);text-align:center;padding-top:38px}
.hero-card h1{font-family:"Lexend",sans-serif;font-weight:600;font-size:50px;line-height:52px;color:var(--ink)}
.hero-card h1 span{color:var(--purple);display:block}
.hero-card p{font-size:16px;line-height:28px;margin:16px 20px 0}
.btn{display:inline-block;background:var(--teal);color:var(--white);font-family:"Lexend",sans-serif;font-weight:500;font-size:25px;border-radius:31px;text-align:center}
.hero-card .btn{width:300px;height:60px;line-height:60px;margin-top:24px}
.dots{left:550px;top:848px;display:flex;gap:14px}
.dots span{width:14px;height:14px;border-radius:50%;background:var(--white)}
.dots span:first-child{background:var(--purple)}
/* teal banners */
.banner{left:75px;width:1050px;height:143px;background:var(--teal);border-radius:12px;color:var(--white)}
.sale{top:1007px;text-align:center;padding-top:22px}
.sale h2{font-family:"Lexend",sans-serif;font-weight:600;font-size:50px}
.sale p{font-size:23px;margin-top:4px}
.pay{top:2591px}
.pay h2{position:absolute;left:78px;top:22px;font-family:"Lexend",sans-serif;font-weight:600;font-size:50px}
.pay p{position:absolute;left:78px;top:88px;font-size:24px}
.partner{position:absolute;left:650px;top:28px;display:flex;align-items:center;gap:24px;font-family:"Lexend",sans-serif;font-weight:600;font-size:68px;color:var(--night)}
.partner i{width:76px;height:76px;border-radius:50%;background:var(--purple);display:block}
/* section heads */
.section-title{left:0;width:1200px;text-align:center;font-family:"Lexend",sans-serif;font-weight:600;font-size:50px;color:var(--ink)}
.section-sub{left:0;width:1200px;text-align:center;font-size:21px}
/* product grid */
.tile{border-radius:0}
/* about */
.about{left:0;top:1907px;width:1200px;height:629px}
.about-text{left:0;width:1200px;text-align:center;color:var(--white)}
.about-text h2{font-family:"Lexend",sans-serif;font-weight:600;font-size:50px}
.about-text p{font-size:20.5px;line-height:39px;width:1080px;margin:22px auto 0}
.about-text .btn{width:300px;height:60px;line-height:60px;margin-top:36px}
/* blog */
.post-title{font-family:"Lexend",sans-serif;font-weight:600;font-size:23px;line-height:31px;width:330px}
.read-more{font-size:15px;color:var(--purple)}
/* footer */
.footer{left:0;top:3320px;width:1200px;height:447px}
.footer .brand{position:absolute;left:75px;top:145px;font-size:46px}
.footer .social{position:absolute;left:75px;top:240px;gap:28px}
.footer .social span{background:var(--white);width:22px;height:22px}
.news-title{left:615px;top:3453px;color:var(--white);font-family:"Lexend",sans-serif;font-weight:500;font-size:30px}
.news-text{left:615px;top:3510px;width:500px;color:var(--white);font-size:14.5px;line-height:25px}
.news-input{left:615px;top:3575px;width:372px;height:50px;border:1px solid #555;color:var(--white);font-size:15px;padding:15px 17px}
.news-btn{left:987px;top:3575px;width:138px;height:50px;background:var(--teal);color:var(--white);font-family:"Lexend",sans-serif;font-weight:500;font-size:19px;text-align:center;line-height:50px}
.copyright{left:0;top:3705px;width:1200px;height:62px;background:var(--night-deep);color:#cfcfcf;font-size:13px;text-align:center;line-height:62px}
.chat{left:1109px;top:3644px;width:64px;height:64px;border-radius:50%;background:var(--teal);box-shadow:0 4px 10px rgba(0,0,0,.3)}
</style>
</head>
<body>

<div class="abs topbar">
  <div class="abs topbar-note">Free shipping on all orders $50 and over!</div>
  <div class="social" aria-label="Social links"><span></span><span></span><span></span><span></span><span></span></div>
</div>

<header class="abs nav">
  <div class="brand"><i></i>Bright Nook</div>
  <nav class="menu"><span>Home</span><span>About Us</span><span>Products</span><span>Blog</span><span>Contact Us</span></nav>
  <div class="cart"></div>
  <div class="cart-count">0</div>
</header>

<svg class="abs hero" viewBox="0 0 1200 778" role="img" aria-label="Woman meditating on a rock by the sea at sunset, arms raised">
  <defs>
    <linearGradient id="sunset" x1="0" y1="0" x2="0" y2="1">
      <stop offset="0" stop-color="#c9944e"/>
      <stop offset=".35" stop-color="var(--sunset-a)"/>
      <stop offset=".65" stop-color="var(--sunset-b)"/>
      <stop offset="1" stop-color="var(--sunset-c)"/>
    </linearGradient>
  </defs>
  <path d="M0 0H1200V710Q600 860 0 710Z" fill="url(#sunset)"/>
</svg>

<div class="abs hero-card">
  <h1>Welcome to<span>YourBrightNook</span></h1>
  <p>Sed ut perspiciatis unde omnis iste natus error sit voluptatem accusantium doloremque laudantium quasi architecto beatae vitae dicta sunt.</p>
  <span class="btn">Shop Now</span>
</div>
<div class="abs dots"><span></span><span></span><span></span><span></span></div>

<div class="abs banner sale">
  <h2>50% off sale going on now!</h2>
  <p>Because saving money also makes us happy.</p>
</div>

<div class="abs section-title" style="top:1215px">Featured Product</div>
<div class="abs section-sub" style="top:1292px">The key to total bliss is nurturing the mind, body, and soul.</div>

<div class="abs tile" style="left:75px;top:1361px;width:226px;height:222px;background:linear-gradient(135deg,#d9b48a,#a0652e)" role="img" aria-label="Candle, bath salts and soap on wood"></div>
<div class="abs tile" style="left:314px;top:1361px;width:227px;height:222px;background:linear-gradient(135deg,#eef0e6,#8aa064)" role="img" aria-label="Oil bottles with green leaves"></div>
<div class="abs tile" style="left:555px;top:1361px;width:227px;height:222px;background:linear-gradient(135deg,#f3f0ee,#e7a3a8)" role="img" aria-label="Cream jars with pink flowers"></div>
<div class="abs tile" style="left:794px;top:1361px;width:331px;height:459px;background:linear-gradient(160deg,#e6ebe9,#8fb3c0 60%,#3c7891)" role="img" aria-label="Woman relaxing in a pool with a towel"></div>
<div class="abs tile" style="left:75px;top:1598px;width:226px;height:222px;background:linear-gradient(135deg,#e2d8cb,#7a4a24)" role="img" aria-label="Amber pump bottles and a brush"></div>
<div class="abs tile" style="left:314px;top:1598px;width:227px;height:222px;background:linear-gradient(135deg,#d7d6d3,#f1f0ec)" role="img" aria-label="White tube and dropper bottles"></div>
<div class="abs tile" style="left:555px;top:1598px;width:227px;height:222px;background:linear-gradient(135deg,#f2b7b6,#e8a0a2)" role="img" aria-label="Hand holding a pink serum bottle"></div>

<svg class="abs about" viewBox="0 0 1200 629" role="img" aria-label="Spa gift box with towels, flowers and bath items under a purple tint">
  <defs>
    <linearGradient id="aboutTint" x1="0" y1="0" x2="1" y2="1">
      <stop offset="0" stop-color="#6a4aa6"/>
      <stop offset=".5" stop-color="var(--lilac)"/>
      <stop offset="1" stop-color="#5b3a95"/>
    </linearGradient>
  </defs>
  <path d="M0 0Q600 130 1200 0V629Q600 490 0 629Z" fill="url(#aboutTint)"/>
</svg>
<div class="abs about-text" style="top:2048px">
  <h2>About Us</h2>
  <p>They say that home is where the heart is. But home is also where your mind and body reside.<br>At Bright Nook we believe that home should be your place of Zen. A respite from the crazy world outside those walls. It is where you recharge your soul so you can approach each day with the focus and energy necessary to conquer the world.</p>
  <span class="btn">Tell Me More</span>
</div>

<div class="abs banner pay">
  <h2>Payment</h2>
  <p>Don’t sweat it. You can pay later</p>
  <div class="partner"><i></i>Crumbly</div>
</div>

<div class="abs section-title" style="top:2783px">The Bright Blog</div>
<div class="abs section-sub" style="top:2862px">Food for the mind, tips for the body and exercises for the soul.</div>

<div class="abs" style="left:75px;top:2933px;width:330px;height:230px;background:linear-gradient(135deg,#3a3330,#c9b7a4)" role="img" aria-label="Couple relaxing at a spa"></div>
<div class="abs" style="left:434px;top:2933px;width:331px;height:230px;background:linear-gradient(135deg,#d8d4ce,#a8968a)" role="img" aria-label="Woman stretching on the beach"></div>
<div class="abs" style="left:794px;top:2933px;width:330px;height:230px;background:linear-gradient(135deg,#eceae4,#6f8a52)" role="img" aria-label="Skincare products with fern leaves"></div>

<div class="abs post-title" style="left:75px;top:3187px">Lorem ipsum dolor sit amet, consectetur adipiscing.</div>
<div class="abs post-title" style="left:434px;top:3187px">Lorem ipsum dolor sit amet, consectetur adipiscing.</div>
<div class="abs post-title" style="left:794px;top:3187px">Lorem ipsum dolor sit amet, consectetur adipiscing.</div>
<div class="abs read-more" style="left:73px;top:3262px">Read More »</div>
<div class="abs read-more" style="left:433px;top:3262px">Read More »</div>
<div class="abs read-more" style="left:792px;top:3262px">Read More »</div>

<footer class="abs footer">
  <svg class="abs" style="left:0;top:0" width="1200" height="447" viewBox="0 0 1200 447" aria-hidden="true">
    <path d="M0 0Q600 140 1200 0V447H0Z" fill="var(--night)"/>
  </svg>
  <div class="brand"><i></i>Bright Nook</div>
  <div class="social" aria-label="Social links"><span></span><span></span><span></span><span></span><span></span></div>
</footer>
<div class="abs news-title">Newsletter Sign-Up</div>
<div class="abs news-text">Lorem ipsum dolor sit amet, consectetur adipiscing eliellentesque tincidunt congue mi et lobortis.</div>
<div class="abs news-input">Enter Email Address</div>
<div class="abs news-btn">Subscribe</div>
<div class="abs copyright">Copyright © 2021, Company Name All Right reserved</div>
<div class="abs chat"></div>

</body>
</html>
```